Roofing company in Toronto, Canada needs a logo design and business card design

We need a business card and logo created for our company. Our company is "KLV Roofing" which provides roofing services for commercial and residential customers. We serve customers in the Greater Toronto Area (in Canada) thus the name KLV.

We want the logo and business card to be a modern design displaying professionalism and quality in the work. We would prefer rounded corners for the business cards but are open to other ideas. The cards should be pleasant and appealing to customers.

Target Market(s)

Commercial and Residential customers

Industry/Entity Type

Roofing

Contact Information for Business Card

Logo Text

KLV Roofing

Requirements
Nice to have
• Colours that are pleasing to the eye but at the same time should stand out from other business cards. If the design can incorporate the name of KLV Roofing and the actual concept of roofing that would be nice.
Should not have
• Do not want the business cards or logo to be childish looking. Need to look professionally designed.

```html
<!DOCTYPE html>
<html lang="en">
<head>
<meta charset="utf-8">
<title>KLV Roofing – Business Card</title>
<link href="https://fonts.googleapis.com/css2?family=Exo+2:wght@400;500;600;700&display=swap" rel="stylesheet">
<style>
  :root {
    --backdrop: #808080;
    --card-black: #050505;
    --brand-red: #c00000;
    --red-top: #b20000;
    --red-bottom: #780000;
    --divider: #5c0a0a;
    --text-white: #ffffff;
    --logo-grey: #9a9a9a;
  }
  * { margin: 0; padding: 0; box-sizing: border-box; }
  html, body { width: 1200px; height: 900px; overflow: hidden; }
  body {
    background: var(--backdrop);
    font-family: "Exo 2", sans-serif;
    position: relative;
  }
  .card {
    position: absolute;
    top: 270px;
    width: 458px;
    height: 283px;
    border-radius: 14px;
    box-shadow: 2px 3px 6px rgba(0,0,0,0.35);
    overflow: hidden;
  }
  .card--front { left: 137px; background: var(--card-black); color: var(--text-white); }
  .card--back {
    left: 626px;
    background: linear-gradient(180deg, var(--red-top), var(--red-bottom));
    display: flex; align-items: center; justify-content: center;
  }
  .wordmark {
    font-weight: 700;
    text-transform: uppercase;
    line-height: 1;
    white-space: nowrap;
  }
  .card--front .wordmark {
    position: absolute;
    right: 27px;
    top: 40px;
    font-size: 40px;
    color: var(--brand-red);
    letter-spacing: 1px;
  }
  .card--back .wordmark {
    font-size: 58px;
    color: var(--text-white);
    letter-spacing: 2px;
  }
  .holder { position: absolute; left: 26px; top: 130px; }
  .holder-name {
    font-size: 19px; font-weight: 600; color: var(--brand-red);
    text-transform: uppercase; letter-spacing: 0.5px; line-height: 1;
  }
  .holder-role { font-size: 15px; font-weight: 500; margin-top: 4px; padding-left: 1px; }
  .divider {
    position: absolute; left: 26px; right: 27px; top: 181px;
    height: 1px; background: var(--divider);
  }
  .contacts { position: absolute; left: 28px; top: 193px; list-style: none; }
  .contacts li {
    display: flex; align-items: center; gap: 9px;
    font-size: 14px; height: 20.5px;
  }
  .contacts svg { width: 11px; height: 11px; fill: var(--brand-red); flex: none; }
  .address {
    position: absolute; right: 27px; top: 202px;
    text-align: right; font-size: 13px; line-height: 17px; font-style: normal;
  }
</style>
</head>
<body>
  <section class="card card--front">
    <div class="wordmark">KLV Roofing</div>
    <div class="holder">
      <p class="holder-name">Mark Ellison</p>
      <p class="holder-role">Director</p>
    </div>
    <div class="divider"></div>
    <ul class="contacts">
      <li>
        <svg viewBox="0 0 12 12" aria-hidden="true"><path d="M3 0h6a1 1 0 0 1 1 1v10a1 1 0 0 1-1 1H3a1 1 0 0 1-1-1V1a1 1 0 0 1 1-1zm0 1.5v8h6v-8zM6 10.2a.6.6 0 1 0 0 1.2.6.6 0 0 0 0-1.2z"/></svg>
        <span>+61-400 555 018</span>
      </li>
      <li>
        <svg viewBox="0 0 12 12" aria-hidden="true"><path d="M0 2h12v8H0zm1 1v.4l5 3.2 5-3.2V3zm0 1.6V9h10V4.6L6 7.8z"/></svg>
        <span>info@klvroofing.com</span>
      </li>
      <li>
        <svg viewBox="0 0 12 12" aria-hidden="true"><path d="M6 0a6 6 0 1 0 0 12A6 6 0 0 0 6 0zm0 1.2c.7.8 1.2 1.9 1.4 3.1H4.6C4.8 3.1 5.3 2 6 1.2zM1.3 5.4h2.2c0 .4 0 .8.1 1.2H1.3a4.8 4.8 0 0 1 0-1.2zm3.3 0h2.8v1.2H4.6zm3.9 0h2.2a4.8 4.8 0 0 1 0 1.2H8.4c.1-.4.1-.8.1-1.2zM4.6 7.7h2.8C7.2 8.9 6.7 10 6 10.8 5.3 10 4.8 8.9 4.6 7.7z"/></svg>
        <span>www.klvroofing.com</span>
      </li>
    </ul>
    <address class="address">
      PO Box 482<br>
      Maplewood<br>
      NSW 2199 AUSTRALIA
    </address>
  </section>

  <section class="card card--back">
    <div class="wordmark">KLV Roofing</div>
  </section>
</body>
</html>
```